Business card for Luxury Portable Restroom Trailer company

We are a Luxury Portable Restroom Trailer Company Called FALCRIDGE HIRES. Based in Orange County California. We provide portable restroom trailers for events, such as, Weddings, Concerts, Charity events, Sporting events, Tournaments, Corporate events, ect. We rent and Sell the Luxury restrooms. Our colors are white, grey, and Orange. As you will see in the logo we uploaded.
There are 2 people in the company so the names and titles will change for the 3 people but card will remain the same. Here is the information for each Person: Dwight Penner CFO 555 318-0476
next Person: Leon Marchetti VP 555 318-0476
Next Person: Owen Marchetti CEO 555 318-0476
Information to include on the card: Luxury Restroom Trailers Rental and Sales. Weddings, Concerts, Charity, Sporting and Corp. Events.

```html
<!DOCTYPE html>
<html lang="en">
<head>
<meta charset="utf-8">
<title>FALCRIDGE HIRES – Business Card</title>
<link href="https://fonts.googleapis.com/css2?family=Open+Sans:wght@400;600;700&display=swap" rel="stylesheet">
<style>
  :root {
    --bg: #242424;
    --card: #2b2b2f;
    --card-deep: #222225;
    --orange: #f26a1f;
    --grey: #9a9a9e;
    --white: #f2f2f2;
  }
  * { margin: 0; padding: 0; box-sizing: border-box; }
  html, body { width: 1200px; height: 768px; overflow: hidden; background: var(--bg); }
  body { font-family: "Open Sans", Arial, sans-serif; position: relative; }

  .card {
    position: absolute; top: 114px; width: 330px; height: 540px;
    border-radius: 22px; background: var(--card); overflow: hidden;
    box-shadow: 0 18px 40px rgba(0,0,0,.55);
  }
  .card--back { left: 230px; }
  .card--front { left: 640px; }

  /* back */
  .back-pattern {
    position: absolute; inset: 0;
    background: linear-gradient(135deg, #6d6d70 0%, #3a3a3d 30%, #1c1c1e 60%, #141416 100%);
  }
  .back-brand {
    position: absolute; top: 118px; left: 250px;
    transform: rotate(90deg); transform-origin: center;
    display: flex; align-items: center; gap: 8px; white-space: nowrap;
    width: 200px; margin-left: -100px;
  }
  .brand-mark { width: 12px; height: 12px; background: var(--orange); flex: none; }
  .brand-name { color: var(--orange); font-weight: 700; font-size: 19px; letter-spacing: 1px; }

  /* front */
  .front-waves { position: absolute; inset: 0; }
  .front-brand {
    position: absolute; top: 52px; left: 0; right: 0;
    display: flex; justify-content: center; align-items: center; gap: 9px;
  }
  .front-brand .brand-name { font-size: 22px; }

  .person { position: absolute; top: 190px; left: 0; right: 0; text-align: center; }
  .person-name { font-size: 26px; font-weight: 700; color: var(--orange); line-height: 1.1; }
  .person-name .surname { color: var(--grey); }
  .person-title { color: var(--white); font-size: 13px; margin-top: 2px; }

  .contact-icons { display: flex; justify-content: center; gap: 8px; margin-top: 10px; }
  .contact-icons svg { width: 24px; height: 24px; }
  .contact-lines { margin-top: 8px; color: var(--white); font-size: 13px; line-height: 1.45; }

  .services {
    position: absolute; left: 24px; right: 18px; bottom: 34px;
    color: var(--white); font-size: 12.5px; line-height: 1.6;
    display: flex; flex-direction: column; gap: 1px;
  }
  .service-row { display: flex; flex-wrap: wrap; column-gap: 12px; list-style: none; }
  .service-row:first-child { padding-left: 46px; }
  .service-row li { list-style: none; white-space: nowrap; display: flex; align-items: center; }
  .service-row li::before {
    content: ""; width: 8px; height: 8px; border-radius: 50%;
    background: var(--orange); margin-right: 5px; flex: none;
  }
</style>
</head>
<body>

  <section class="card card--back">
    <div class="back-pattern" role="img" aria-label="Repeating brand symbol pattern with a silver-to-black sheen"></div>
    <div class="back-brand">
      <span class="brand-mark"></span>
      <span class="brand-name">FALCRIDGE HIRES</span>
    </div>
  </section>

  <section class="card card--front">
    <svg class="front-waves" viewBox="0 0 330 540" preserveAspectRatio="none" aria-hidden="true">
      <path d="M0 330 Q170 390 330 250 L330 540 L0 540 Z" fill="#262629"/>
      <path d="M0 400 Q180 420 330 330 L330 540 L0 540 Z" fill="#29292c"/>
      <path d="M0 450 Q200 450 330 380 L330 540 L0 540 Z" fill="#232326"/>
    </svg>

    <div class="front-brand">
      <span class="brand-mark"></span>
      <span class="brand-name">FALCRIDGE HIRES</span>
    </div>

    <div class="person">
      <h1 class="person-name">Dwight <span class="surname">Penner</span></h1>
      <p class="person-title">CFO</p>
      <div class="contact-icons">
        <svg viewBox="0 0 24 24" aria-label="Phone"><circle cx="12" cy="12" r="12" fill="var(--orange)"/><path d="M8 6.5l2 0 1 3-1.3 1a7 7 0 0 0 3.8 3.8l1-1.3 3 1v2c0 .8-.7 1.5-1.5 1.5A10.5 10.5 0 0 1 6.5 8c0-.8.7-1.5 1.5-1.5z" fill="#fff"/></svg>
        <svg viewBox="0 0 24 24" aria-label="Email"><circle cx="12" cy="12" r="12" fill="var(--orange)"/><rect x="6" y="8" width="12" height="8.5" rx="1" fill="none" stroke="#fff" stroke-width="1.5"/><path d="M6.5 8.5l5.5 4.3 5.5-4.3" fill="none" stroke="#fff" stroke-width="1.5"/></svg>
        <svg viewBox="0 0 24 24" aria-label="Website"><circle cx="12" cy="12" r="12" fill="var(--orange)"/><circle cx="12" cy="12" r="6" fill="none" stroke="#fff" stroke-width="1.4"/><ellipse cx="12" cy="12" rx="2.6" ry="6" fill="none" stroke="#fff" stroke-width="1.2"/><path d="M6 12h12" stroke="#fff" stroke-width="1.2"/></svg>
      </div>
      <div class="contact-lines">
        <p>555 318-0476</p>
        <p>info@falcridgehires.com</p>
        <p>www.falcridgehires.com</p>
      </div>
    </div>

    <div class="services">
      <ul class="service-row">
        <li>Weddings</li>
        <li>Concerts</li>
      </ul>
      <ul class="service-row">
        <li>Charity</li>
        <li>Sporting and Corp</li>
        <li>Events</li>
      </ul>
      <ul class="service-row">
        <li>Luxury Restroom Trailers Rental and Sales</li>
      </ul>
    </div>
  </section>

</body>
</html>
```